Need App for Impact Related Events

My app is to help with internal events. When you enter the prompted event code the next screen shows you everyone currently at the event. It will give you the ability to Start a conversation with someone you met at that event, or signal it is your turn to send a message. The next screen is a message thread with that person. I am looking for a design that incorporates the colors and ‘feel good’ emotion of our logo. I have pieced together a pretty good interpretation of what I’m looking for in the attached mockup by slicing and dicing designs. I also attached our logo mascot.Screens (see attached mockups)

Note 1: I do not like the picture on the screen used in screen one because it makes it seem like a dating app. I attached an alternative photo that can be used or present different ideas.

Note 2: On the login/signup screen (screen 2) I need an additional first and last name for login, you can try to fit this on one login screen or present a two step signup screen where that is presented in the second screen.

READ MOCKUP GUIDELINES UNDER Must Haves

Target Market(s)

People attending internal social impact events

Industry/Entity Type

Charity

Font styles to use
Sans Serif

Colors
86cfc6

Requirements
Must have
• Follow the screen mockups attached to project
• PLEASE READ
• I have provided a relatively close design of what I’m looking for in the mockups. Some screens need to be followed more closely to my design mockup than other. I have listed a guide below how how closely you should follow my mockup design exactly. Overall I would like to see some ideas of incorporating a few accent colors so it doesn’t appear SO Blue. I also attached some app inspiration designs I found from around the web
• Screen Mockup Guideline Follow %
• Screen 1: 65% - mostly on target, would like to see ways to make it not SO Blue and possibly creative places to add some explainer text describing the app
• Screen 2: 50% - general design idea is here, but more open
• Screen 3: 35% - a lot more room for design influence
• Screen 4: 70% - mostly on target, a little room for design influence/color scheme ideas
• Screen 5-6: 25% - a lot of room for design change/ideas/influence
• Screen 7-8: 80% - already very close to what I need, maybe open to slight sizing and color scheme ideas
• Screen 9: 15% - the most open for influence, only the general functionality of the screen is communicated here
Nice to have
• Please Read Mockup Guideline above. In large part I am looking for something to use some nice accent colors so it is not overwhelmingly blue and bring the whole design into a seamless style.
Should not have

```html
<!DOCTYPE html>
<html lang="en">
<head>
<meta charset="utf-8">
<title>KindHive – App Screens 5 to 8</title>
<link rel="stylesheet" href="https://fonts.googleapis.com/css2?family=Poppins:wght@400;500;600&display=swap">
<style>
  :root{
    --bg:#efefef;
    --screen:#ffffff;
    --teal:#1ccfcf;
    --teal-soft:#d9f6f1;
    --mint:#2fe0b4;
    --ink:#1e1e1e;
    --text:#4a4a4a;
    --muted:#8a8a8a;
    --line:#e6e6e6;
    --bubble-grey:#f1f1f1;
    --mascot-dark:#2b1d12;
    --accent-blue:#8fb8ef;
    --accent-pink:#e66aa6;
  }
  *{box-sizing:border-box;margin:0;padding:0}
  html,body{width:1200px;height:1200px;overflow:hidden}
  body{background:var(--bg);font-family:"Poppins",sans-serif;color:var(--text);position:relative}
  .abs{position:absolute}
  .mascot{position:absolute;border-radius:50%;background:radial-gradient(circle at 40% 40%,var(--teal) 0 45%,var(--mascot-dark) 46% 100%)}
  .brand{left:714px;top:176px;width:330px;text-align:center;font-size:56px;font-weight:500;color:var(--ink);letter-spacing:1px}
  .step{top:388px;width:40px;text-align:center;font-size:18px;font-weight:600;color:var(--ink)}
  .screen{position:absolute;top:456px;width:228px;height:494px;background:var(--screen);border-radius:24px;overflow:hidden}
  .screen.tall{height:536px}
  .time{left:20px;top:14px;font-size:9px;color:var(--muted)}
  .home-bar{left:72px;width:84px;height:3px;border-radius:2px;background:#cfcfcf}
  .back{left:12px;top:48px;width:12px;height:14px}
  .title{left:32px;top:40px;font-size:13px;line-height:20px;letter-spacing:.6px;color:var(--ink);font-weight:400}
  .title b{font-weight:600}
  .deco-circle{position:absolute;border-radius:50%;background:var(--teal-soft)}
  .field{background:#fff;border-radius:6px;box-shadow:0 4px 14px rgba(0,0,0,.07);font-size:10px;color:var(--ink);display:flex;align-items:center;justify-content:center}
  .go-button{left:82px;top:293px;width:64px;height:64px;border-radius:50%;background:linear-gradient(135deg,var(--teal),var(--mint));box-shadow:0 8px 18px rgba(28,207,207,.35);display:flex;align-items:center;justify-content:center}
  .search{left:24px;top:96px;font-size:9px;color:var(--muted);display:flex;align-items:center;gap:10px}
  .rule{height:1px;background:var(--line)}
  .contact{left:9px;width:219px;height:63px}
  .contact .marker{position:absolute;left:0;top:12px;width:2px;height:40px;background:#c9c9c9}
  .avatar{position:absolute;border-radius:50%;background:linear-gradient(150deg,#c9b39f,#5b4a3f)}
  .online{position:absolute;width:8px;height:8px;border-radius:50%;background:var(--teal);border:1.5px solid #fff}
  .contact .name{position:absolute;left:57px;font-size:12px;color:var(--text)}
  .contact .preview{position:absolute;left:58px;top:38px;font-size:7px;color:var(--muted);white-space:nowrap}
  .action{position:absolute;left:155px;top:17px;width:43px;height:30px;background:var(--mint);color:#fff;font-size:6px;display:flex;flex-direction:column;align-items:center;justify-content:center;gap:2px}
  .action.turn{background:var(--teal)}
  .chevron{position:absolute;left:185px;top:26px;width:6px;height:10px}
  .hidden-row{left:20px;top:466px;font-size:12px;letter-spacing:.5px;color:var(--text)}
  .thread-head{left:0;top:0;width:228px;height:90px;background:#fff}
  .thread-body{left:0;top:90px;width:228px;height:344px;background:#f8f8f8}
  .bubble{position:absolute;width:182px;height:39px;border-radius:6px;font-size:8px;display:flex;align-items:center;padding:0 12px}
  .bubble.in{left:10px;background:var(--bubble-grey);color:var(--text)}
  .bubble.out{left:36px;background:var(--teal);color:#fff;line-height:13px;font-weight:500}
  .stamp{position:absolute;font-size:6.5px;color:var(--ink)}
  .composer{left:20px;top:444px;font-size:8.5px;color:var(--muted)}
  .kind-label{left:0;top:187px;width:228px;text-align:center;font-size:12px;letter-spacing:.6px;color:var(--text)}
  .kind-code{left:22px;top:222px;width:184px;height:38px;font-size:17px;letter-spacing:1px;font-weight:500}
  .kind-note{left:0;top:276px;width:228px;text-align:center;font-size:10px;line-height:18.4px;color:var(--text);letter-spacing:.3px}
</style>
</head>
<body>

<div class="mascot" style="left:828px;top:36px;width:120px;height:110px" role="img" aria-label="Cheerful cartoon bee mascot flying"></div>
<div class="abs brand">KindHive</div>

<div class="abs step" style="left:142px">5</div>
<div class="abs step" style="left:436px">6</div>
<div class="abs step" style="left:727px">7</div>
<div class="abs step" style="left:1022px">8</div>

<!-- Screen 5: enter location code -->
<section class="screen" style="left:65px">
  <div class="deco-circle" style="left:160px;top:20px;width:90px;height:90px;opacity:.35"></div>
  <div class="deco-circle" style="left:186px;top:348px;width:90px;height:110px"></div>
  <div class="deco-circle" style="left:4px;top:400px;width:18px;height:18px"></div>
  <div class="deco-circle" style="left:36px;top:404px;width:8px;height:8px"></div>
  <span class="abs time">9:41</span>
  <svg class="abs back" viewBox="0 0 12 14"><path d="M8 2 L3 7 L8 12" stroke="var(--teal)" stroke-width="1.6" fill="none"/></svg>
  <div class="abs title">ENTER LOCATION<br><b>KIND CODE</b></div>
  <div class="mascot" style="left:96px;top:108px;width:38px;height:36px" role="img" aria-label="Small bee mascot"></div>
  <div class="abs field" style="left:22px;top:228px;width:184px;height:38px">Enter code here</div>
  <div class="abs go-button">
    <svg width="24" height="20" viewBox="0 0 24 20"><path d="M2 10 H21 M14 3 L21 10 L14 17" stroke="#fff" stroke-width="2" fill="none" stroke-linecap="round"/></svg>
  </div>
  <div class="abs home-bar" style="top:484px"></div>
</section>

<!-- Screen 6: who you've met so far -->
<section class="screen tall" style="left:352px">
  <div class="deco-circle" style="left:200px;top:360px;width:60px;height:110px"></div>
  <span class="abs time">9:41</span>
  <svg class="abs back" viewBox="0 0 12 14"><path d="M8 2 L3 7 L8 12" stroke="var(--teal)" stroke-width="1.6" fill="none"/></svg>
  <div class="abs title">WHO YOU'VE<br><b>MET SO FAR</b></div>
  <div class="mascot" style="left:136px;top:56px;width:18px;height:18px" role="img" aria-label="Small bee mascot"></div>
  <svg class="abs" style="left:198px;top:40px" width="14" height="14" viewBox="0 0 14 14"><circle cx="7" cy="7" r="5" fill="var(--teal)"/><circle cx="7" cy="7" r="2" fill="#fff"/></svg>
  <div class="abs search">
    <svg width="12" height="12" viewBox="0 0 12 12"><circle cx="5" cy="5" r="4" stroke="var(--teal)" stroke-width="1.3" fill="none"/><path d="M8 8 L11 11" stroke="var(--teal)" stroke-width="1.3"/></svg>
    Search name
  </div>
  <div class="abs rule" style="left:14px;top:120px;width:214px"></div>

  <div class="abs contact" style="top:137px">
    <span class="marker" style="background:var(--accent-blue)"></span>
    <span class="avatar" style="left:12px;top:14px;width:36px;height:36px" role="img" aria-label="Profile photo"></span>
    <span class="online" style="left:41px;top:12px"></span>
    <span class="name" style="top:24px">Nora K. Hale</span>
    <span class="action"><svg width="9" height="9" viewBox="0 0 9 9"><path d="M1 1 L8 4.5 L1 8 Z" stroke="#fff" fill="none"/></svg>Start</span>
  </div>
  <div class="abs rule" style="left:9px;top:200px;width:219px"></div>
  <div class="abs contact" style="top:201px">
    <span class="marker" style="background:var(--accent-pink)"></span>
    <span class="avatar" style="left:12px;top:14px;width:36px;height:36px" role="img" aria-label="Profile photo"></span>
    <span class="online" style="left:41px;top:12px"></span>
    <span class="name" style="top:24px">Lena Marsh</span>
    <span class="action turn"><svg width="9" height="9" viewBox="0 0 9 9"><path d="M2 8 V4 H7 M5 2 L7 4 L5 6" stroke="#fff" fill="none"/></svg>Your Turn</span>
  </div>
  <div class="abs rule" style="left:9px;top:264px;width:219px"></div>
  <div class="abs contact" style="top:264px">
    <span class="marker"></span>
    <span class="avatar" style="left:12px;top:14px;width:36px;height:36px" role="img" aria-label="Profile photo"></span>
    <span class="online" style="left:41px;top:12px;background:#cfcfcf"></span>
    <span class="name" style="top:16px">Owen R. Pike</span>
    <span class="preview" style="top:34px">Lorem Ipsum is simply dum...</span>
    <svg class="chevron" viewBox="0 0 6 10"><path d="M1 1 L5 5 L1 9" stroke="var(--text)" fill="none"/></svg>
  </div>
  <div class="abs rule" style="left:9px;top:327px;width:219px"></div>
  <div class="abs contact" style="top:327px">
    <span class="marker"></span>
    <span class="avatar" style="left:12px;top:14px;width:36px;height:36px" role="img" aria-label="Profile photo"></span>
    <span class="online" style="left:41px;top:12px"></span>
    <span class="name" style="top:16px">Miles T. Carver</span>
    <span class="preview" style="top:34px">Standard dummy text ever ...</span>
    <svg class="chevron" viewBox="0 0 6 10"><path d="M1 1 L5 5 L1 9" stroke="var(--text)" fill="none"/></svg>
  </div>
  <div class="abs rule" style="left:9px;top:390px;width:219px"></div>
  <div class="abs contact" style="top:390px">
    <span class="marker"></span>
    <span class="avatar" style="left:12px;top:14px;width:36px;height:36px" role="img" aria-label="Profile photo"></span>
    <span class="online" style="left:41px;top:12px"></span>
    <span class="name" style="top:16px">Ravi Osei</span>
    <span class="preview" style="top:34px">Standard dummy text ever ...</span>
    <svg class="chevron" viewBox="0 0 6 10"><path d="M1 1 L5 5 L1 9" stroke="var(--text)" fill="none"/></svg>
  </div>
  <div class="abs rule" style="left:9px;top:452px;width:219px"></div>
  <div class="abs hidden-row">HIDDEN (52)</div>
  <svg class="abs" style="left:190px;top:471px" width="10" height="6" viewBox="0 0 10 6"><path d="M1 1 L5 5 L9 1" stroke="var(--text)" fill="none"/></svg>
  <div class="abs home-bar" style="top:526px"></div>
</section>

<!-- Screen 7: message thread -->
<section class="screen" style="left:638px">
  <div class="abs thread-head"></div>
  <div class="abs thread-body"></div>
  <span class="abs time">9:41</span>
  <svg class="abs back" viewBox="0 0 12 14"><path d="M8 2 L3 7 L8 12" stroke="var(--teal)" stroke-width="1.6" fill="none"/></svg>
  <div class="abs title"><b>LENA MARSH</b></div>
  <div class="mascot" style="left:196px;top:40px;width:18px;height:18px" role="img" aria-label="Small bee mascot"></div>
  <span class="avatar" style="left:87px;top:64px;width:52px;height:52px;border:2px solid var(--teal)" role="img" aria-label="Profile photo of conversation partner"></span>
  <span class="online" style="left:130px;top:64px"></span>

  <div class="bubble in" style="top:134px">Who you've met so far</div>
  <span class="stamp" style="left:16px;top:180px">1 day ago</span>
  <div class="bubble out" style="top:198px">Lorem Ipsum has been the industry's standard dummy text ever</div>
  <span class="stamp" style="right:10px;top:244px">1 day ago</span>
  <div class="bubble in" style="top:262px">Who you've met so far</div>
  <span class="stamp" style="left:16px;top:307px">1 day ago</span>
  <div class="bubble out" style="top:325px">Lorem Ipsum has been the industry's standard dummy text ever</div>
  <span class="stamp" style="right:10px;top:371px">Yesterday 5:23</span>

  <div class="abs composer">Type your message here</div>
  <svg class="abs" style="left:190px;top:442px" width="16" height="14" viewBox="0 0 16 14"><path d="M1 7 L15 1 L11 13 L8 8 Z" fill="var(--teal)"/></svg>
  <div class="abs rule" style="left:14px;top:462px;width:200px"></div>
  <div class="abs home-bar" style="top:484px"></div>
</section>

<!-- Screen 8: your kind code -->
<section class="screen" style="left:927px">
  <div class="deco-circle" style="left:140px;top:20px;width:110px;height:90px;opacity:.35"></div>
  <div class="deco-circle" style="left:146px;top:58px;width:16px;height:16px"></div>
  <div class="deco-circle" style="left:186px;top:348px;width:90px;height:110px"></div>
  <div class="deco-circle" style="left:4px;top:400px;width:18px;height:18px"></div>
  <div class="deco-circle" style="left:36px;top:404px;width:8px;height:8px"></div>
  <div class="mascot" style="left:96px;top:86px;width:38px;height:36px" role="img" aria-label="Small bee mascot"></div>
  <div class="abs kind-label">YOUR KIND CODE</div>
  <div class="abs field kind-code">JGHEYS747JRH</div>
  <p class="abs kind-note">Give this code to the people<br>at your location or event to allow<br>them to connect to each<br>other - kind of like a wifi password</p>
  <div class="abs home-bar" style="top:484px"></div>
</section>

</body>
</html>
```